Business Card Design Project

We need a Business Card for an Mechanical Engineering firm in Singapore. The design should be Modern & Technical looking, yet eye catching.

Our company deals in Cutting Tools & Machine Accessories for the Manufacturing Industries such as Oil & Gas, Aero Space, etc... For more information on our Company, you can either email me or view our website www.torvalen.com.sg.

We are trying to revamp our image to give our consumers a fresh new perspective to our company, so we welcome all ideas.

Industry/Entity Type

Business

Requirements
Must have
• Must incorporate New Company Logo into the card as shown in Uploaded file.

```html
<!DOCTYPE html>
<html lang="en">
<head>
<meta charset="utf-8">
<title>Torvalen Tools – Business Card</title>
<link rel="stylesheet" href="https://fonts.googleapis.com/css2?family=Ubuntu:wght@400;500&display=swap">
<style>
  :root {
    --backdrop: #e4e5e6;
    --card: #ffffff;
    --brand-red: #951b32;
    --ink: #3a1020;
    --white: #ffffff;
  }
  * { box-sizing: border-box; margin: 0; padding: 0; }
  html, body {
    width: 1200px;
    height: 900px;
    overflow: hidden;
    background: var(--backdrop);
    font-family: "Ubuntu", sans-serif;
    color: var(--ink);
  }
  .canvas { position: relative; width: 1200px; height: 900px; }

  .card {
    position: absolute;
    left: 269px;
    width: 662px;
    height: 377px;
    background: var(--card);
    overflow: hidden;
  }
  .card--front { top: 45px; }
  .card--back { top: 478px; }

  .rule {
    position: absolute;
    left: 0;
    width: 269px;
    height: 5px;
    background: var(--brand-red);
  }
  .rule--title { top: 109px; }
  .rule--web-top { top: 237px; }
  .rule--web-bottom { top: 297px; }

  .holder { position: absolute; right: 393px; top: 36px; text-align: right; }
  .holder__name { font-size: 31px; font-weight: 400; line-height: 1.2; color: var(--ink); }
  .holder__role { font-size: 19px; line-height: 1.2; color: var(--brand-red); margin-top: 2px; }

  .contact {
    position: absolute;
    top: 154px;
    left: 0;
    width: 400px;
    display: grid;
    grid-template-columns: 269px auto;
    column-gap: 20px;
    row-gap: 2px;
    font-size: 16px;
    line-height: 20px;
  }
  .contact__value { text-align: right; color: var(--ink); }
  .contact__label { color: var(--brand-red); }

  .web {
    position: absolute;
    right: 393px;
    top: 256px;
    font-size: 20px;
    line-height: 24px;
    letter-spacing: 1px;
    white-space: nowrap;
    color: var(--ink);
  }

  .brand {
    position: absolute;
    left: 289px;
    width: 349px;
    top: 254px;
    height: 48px;
    display: flex;
    align-items: center;
    justify-content: flex-end;
    gap: 10px;
  }
  .brand__dot {
    flex: none;
    width: 24px;
    height: 24px;
    border-radius: 50%;
    background: var(--brand-red);
  }
  .brand__name {
    font-size: 32px;
    font-weight: 500;
    line-height: 1;
    white-space: nowrap;
    text-transform: uppercase;
    color: var(--brand-red);
  }

  .address {
    position: absolute;
    left: 26px;
    right: 24px;
    top: 339px;
    font-size: 19px;
    line-height: 24px;
    white-space: nowrap;
    color: var(--ink);
  }

  .band-line {
    position: absolute;
    left: 0;
    width: 100%;
    height: 4px;
    background: var(--brand-red);
  }
  .band-line--top { top: 151px; }
  .band-line--bottom { top: 218px; }
  .band {
    position: absolute;
    left: 0;
    top: 162px;
    width: 100%;
    height: 52px;
    background: var(--brand-red);
    display: flex;
    align-items: center;
    justify-content: center;
  }
  .band__web {
    font-size: 25px;
    letter-spacing: 1.5px;
    color: var(--white);
  }
</style>
</head>
<body>
<main class="canvas">
  <section class="card card--front" aria-label="Business card front">
    <div class="holder">
      <h1 class="holder__name">Marcus Tan</h1>
      <p class="holder__role">President/CEO</p>
    </div>
    <div class="rule rule--title"></div>

    <div class="contact">
      <span class="contact__value">65-61234578</span>
      <span class="contact__label">mobile</span>
      <span class="contact__value">info@torvalen.com.sg</span>
      <span class="contact__label">email</span>
    </div>

    <div class="rule rule--web-top"></div>
    <p class="web">www.torvalen.com.sg</p>
    <div class="rule rule--web-bottom"></div>

    <div class="brand">
      <span class="brand__dot"></span>
      <span class="brand__name">Torvalen Tools</span>
    </div>

    <p class="address">27 Kallang Way #03-12, Meridian Industrial Hub, Singapore 349281</p>
  </section>

  <section class="card card--back" aria-label="Business card back">
    <div class="band-line band-line--top"></div>
    <div class="band"><span class="band__web">www.torvalen.com.sg</span></div>
    <div class="band-line band-line--bottom"></div>
  </section>
</main>
</body>
</html>
```